Business Card/ Email Signature Design Project

I am an Interior Designer. I need a business card that looks sophisticated stylish but simple in design. My work covers space design/ interior architecture/ furniture design/ product development & styling.

I have a very specific brief and know mostly what I want. I'm hoping to work with someone who can translate my ideas.

My branding should have a strong focus on my name, the majority of my work is referral based.
I'm keen to keep a monochromatic colour scheme: dark charcoal/ black/ white/ embossing/ silver. I'm not suggesting we use all that I've listed, they are possible ideas at this stage. I will need to be mindful of printing costs an also how I make the design work across, cards, letter heads, email logo and web design.

Theory behind images sent below;
1-Rug Image_(minus boarder) I was thinking this image could be used on the back of the card with my contact details over. I like that the lines are almost hand drawn and start to look free form. It's a subtle contrast to a more formal front of the card with my name.
2_Tomas Dreyer_I really like the orientation, the proportion of font on the card, the colour and the font. I like the lower case for my name and the upper case for 'Interior Design'. Not sure if it should be 'Interior Designer or Interior Design' at this stage, was leaning towards 'Interior Design'. Was thinking the 'i' and 'd' in my surname could be the colour eg 'silver'?? We can decide on this once we see it.

Look forward to hearing from you.
Cheers,
Noreen Balfour

Printing

Noreen Balfour Interior Design

```html
<!DOCTYPE html>
<html lang="en">
<head>
<meta charset="utf-8">
<title>Noreen Balfour Interior Design — Business Card</title>
<link rel="stylesheet" href="https://fonts.googleapis.com/css2?family=Inter:wght@100;200;300&display=swap">
<style>
  :root {
    --backdrop: #e7e4e0;
    --card-dark: #161616;
    --card-mid: #2c2c2c;
    --ink-light: #d9d9d9;
    --ink-soft: #a9a9a9;
    --ink-muted: #6a6a6a;
    --glow: rgba(255, 255, 255, 0.16);
  }
  * { margin: 0; padding: 0; box-sizing: border-box; }
  html, body {
    width: 1200px;
    height: 750px;
    overflow: hidden;
    background: var(--backdrop);
    font-family: "Inter", "Helvetica Neue", Arial, sans-serif;
  }
  .sheet {
    width: 1200px;
    height: 750px;
    display: flex;
    align-items: center;
    justify-content: center;
    gap: 40px;
  }
  .card {
    position: relative;
    width: 560px;
    height: 350px;
    overflow: hidden;
    background: radial-gradient(ellipse at 50% 60%, var(--card-mid) 0%, var(--card-dark) 75%);
  }
  .card-back .contact {
    position: absolute;
    left: 40px;
    top: 34px;
    list-style: none;
    font-weight: 300;
    font-size: 12.5px;
    line-height: 15px;
    letter-spacing: 0.42em;
    text-transform: uppercase;
    color: var(--ink-light);
  }
  .card-back .contact .phone { color: var(--ink-muted); }
  .card-front .glow-band {
    position: absolute;
    left: 0;
    right: 0;
    top: 150px;
    height: 34px;
    background: radial-gradient(ellipse at 55% 50%, var(--glow) 0%, rgba(255,255,255,0.05) 45%, transparent 75%);
  }
  .card-front .name {
    position: absolute;
    left: 0;
    right: 0;
    top: 128px;
    text-align: center;
    padding-left: 70px;
    font-weight: 100;
    font-size: 54px;
    letter-spacing: -0.01em;
    color: var(--ink-light);
    white-space: nowrap;
  }
  .card-front .discipline {
    position: absolute;
    left: 0;
    right: 0;
    top: 205px;
    text-align: center;
    padding-left: 70px;
    font-weight: 200;
    font-size: 14px;
    letter-spacing: 0.32em;
    text-transform: uppercase;
    color: var(--ink-muted);
  }
</style>
</head>
<body>
  <main class="sheet">
    <section class="card card-back" aria-label="Card back with contact details">
      <ul class="contact">
        <li>P.O Box 214 Elmwood VIC. 3071</li>
        <li>interiors@noreenbalfour.com</li>
        <li>www.noreenbalfour.com</li>
        <li class="phone">0400-555-271</li>
      </ul>
    </section>
    <section class="card card-front" aria-label="Card front with name">
      <div class="glow-band"></div>
      <h1 class="name">noreen balfour</h1>
      <p class="discipline">Interior Design</p>
    </section>
  </main>
</body>
</html>
```